Australian Trucking Company Requires Professional Looking Stationary

We require a professional looking stationary design that incorporates our newly designed logo.

Our business, called "Brell Haulage Contracting", provides contracting work, transport and logistics to business in Western Australia particularly with links to the mining sector.

We are a small business looking to expand and our new logo and our new stationary will help develop our brand image in our market place.

Target Market(s)

Businesses and Corporation with links to the Mining Sector

Industry/Entity Type

Small Business

Requirements
Must have
• The letterhead must have the following details:
The new logo

Text saying: "Brell Holdings Pty Ltd (ACN 582 316 907) ATF The Brell Discretionary Trust T/AS"
"ABN 71 834 209 553"
Address "P.O Box 817 Wattlegrove WA, 6958"
Phone: 08 9352 7140
Email: brellhaul@mailbox-example.com.au

The text on the letterhead should be editable as the details are likely to change in the near future. Provision should be made for a website address all though one isn't available at the moment.

The styling, layout and font text is entirely up to the designer.

```html
<!DOCTYPE html>
<html lang="en">
<head>
<meta charset="utf-8">
<title>Brell Haulage Contracting – Business Card</title>
<link rel="stylesheet" href="https://fonts.googleapis.com/css2?family=Arimo:wght@400;700&display=swap">
<style>
  :root {
    --stage: #d9d4cc;
    --card-white: #ffffff;
    --brand-red: #c8161d;
    --brand-red-deep: #7d0008;
    --brand-red-bright: #e81c24;
    --ink: #3c3c3c;
    --ink-soft: #6a6a6a;
    --mark-grey: #7a7a7a;
    --mark-silver: #d6d7d9;
    --white: #ffffff;
  }
  * { box-sizing: border-box; margin: 0; padding: 0; }
  html, body { width: 1200px; height: 1200px; overflow: hidden; }
  body {
    background: var(--stage);
    font-family: "Arimo", Arial, sans-serif;
    position: relative;
  }
  .card {
    position: absolute;
    width: 840px;
    height: 480px;
    overflow: hidden;
    box-shadow: 0 4px 14px rgba(0,0,0,.25);
  }
  .card-front { left: 84px; top: 78px; background: var(--card-white); }
  .card-back {
    left: 284px; top: 650px;
    background: radial-gradient(circle at 47% 53%, var(--brand-red-bright) 0%, #a60a12 38%, var(--brand-red-deep) 80%);
  }
  .brand-mark {
    position: absolute;
    left: 62px; top: 40px;
    width: 150px; height: 150px;
    background: var(--mark-grey);
  }
  .brand-mark-large {
    position: absolute;
    left: 556px; top: 64px;
    width: 260px; height: 260px;
    background: var(--mark-silver);
  }
  .abn {
    position: absolute; right: 28px; top: 28px;
    font-size: 24px; color: var(--ink-soft);
  }
  .brand-name {
    position: absolute; left: 262px; top: 54px;
    font-size: 50px; font-weight: 700; line-height: 1.08;
    color: var(--brand-red); text-transform: uppercase;
  }
  .contact-list {
    position: absolute; left: 134px; top: 232px;
    list-style: none;
  }
  .contact-list li {
    display: flex; align-items: center;
    height: 33.5px;
    font-size: 22px; color: var(--ink);
  }
  .contact-list svg { width: 18px; height: 18px; margin-right: 10px; fill: var(--brand-red); flex: none; }
  .wave { position: absolute; left: 0; top: 0; width: 840px; height: 480px; }
  .holder {
    position: absolute; right: 90px; top: 392px; text-align: right; color: var(--white);
  }
  .holder-name { font-size: 31px; font-weight: 700; }
  .holder-title { font-size: 24px; letter-spacing: 2px; margin-top: 8px; }
  .entity {
    position: absolute; right: 294px; top: 340px;
    text-align: right; color: var(--white);
    font-size: 22px; line-height: 30px;
  }
  .site {
    position: absolute; right: 294px; top: 412px;
    color: var(--white); font-size: 28px; letter-spacing: 2px;
  }
  .site strong { font-weight: 700; }
</style>
</head>
<body>

<section class="card card-front" aria-label="Business card front">
  <svg class="wave" viewBox="0 0 840 480" aria-hidden="true">
    <defs>
      <linearGradient id="redBand" x1="0" x2="1" y1="0" y2="0">
        <stop offset="0" stop-color="#9e0a10"/>
        <stop offset=".45" stop-color="#e81c24"/>
        <stop offset="1" stop-color="#7d0008"/>
      </linearGradient>
      <linearGradient id="silverSwoosh" x1="0" x2="1">
        <stop offset="0" stop-color="#f2f2f2"/>
        <stop offset=".2" stop-color="#222"/>
        <stop offset=".35" stop-color="#e6e6e6"/>
        <stop offset=".6" stop-color="#333"/>
        <stop offset=".8" stop-color="#ffffff"/>
      </linearGradient>
    </defs>
    <path d="M0 374 C100 410 200 436 300 432 C420 428 520 370 640 366 C720 364 790 390 840 414 L840 480 L0 480 Z" fill="url(#redBand)"/>
    <path d="M0 352 C100 394 200 420 300 418 C420 416 520 372 640 358" fill="none" stroke="url(#silverSwoosh)" stroke-width="6"/>
  </svg>

  <div class="brand-mark" role="img" aria-label="Company logo symbol"></div>
  <p class="abn">ABN 71 834 209 553</p>
  <h1 class="brand-name">Brell<br>Haulage<br>Contracting</h1>

  <ul class="contact-list">
    <li><svg viewBox="0 0 24 24"><path d="M6.6 10.8a15 15 0 0 0 6.6 6.6l2.2-2.2a1 1 0 0 1 1-.25 11.4 11.4 0 0 0 3.6.57 1 1 0 0 1 1 1V20a1 1 0 0 1-1 1A17 17 0 0 1 3 4a1 1 0 0 1 1-1h3.5a1 1 0 0 1 1 1c0 1.25.2 2.45.57 3.57a1 1 0 0 1-.25 1z"/></svg>08 9352 7140</li>
    <li><svg viewBox="0 0 24 24"><path d="M2 5h20v2l-10 6L2 7z M2 9l10 6 10-6v10H2z"/></svg>brellhaul@mailbox-example.com.au</li>
    <li><svg viewBox="0 0 24 24"><circle cx="12" cy="12" r="9" fill="none" stroke="#c8161d" stroke-width="2"/><path d="M3 12h18M12 3c3 3 3 15 0 18M12 3c-3 3-3 15 0 18" fill="none" stroke="#c8161d" stroke-width="1.6"/></svg>www.brellhaul.com</li>
    <li><svg viewBox="0 0 24 24"><path d="M12 3 2 12h3v8h5v-5h4v5h5v-8h3z"/></svg>P.O Box 817 Wattlegrove WA, 6958</li>
  </ul>

  <div class="holder">
    <p class="holder-name">Your Name</p>
    <p class="holder-title">Title</p>
  </div>
</section>

<section class="card card-back" aria-label="Business card back">
  <div class="brand-mark-large" role="img" aria-label="Large company logo symbol"></div>
  <p class="entity">Brell Holdings Pty Ltd (ACN 582 316 907)<br>ATF The Brell Discretionary Trust T/AS</p>
  <p class="site">www.<strong>brellhaul</strong>.com</p>
</section>

</body>
</html>
```